Book Cover Design for Millennial

I need a book cover design for my book Quiet Summit. The subtitle of the book is Steps for Building a Life You Savor at the Office.

I'm a career coach who helps millennial career professionals. I myself am a millennial but on the older end (34). I've dealt and been through most of the challenges millennials are facing as career professionals and I wrote this book with the thought of providing guidance and aid to getting past those challenges and shedding light on fundamental habits and practices that will help them excel in their careers. In addition, the book will help them prepare millennials for our turn as the leaders, managers, etc moving forward in corporate America. The final design should have the main title of the book in it as the focal point but not the subtitle. I want the cover to communicate something NEW, Bold, Youthful, non-traditional. I want it to stick out while still maintaining a sleek and Professional look.
Updates

Hello, Designers! I want to thank you all for your submissions! The work is amazing and I greatly appreciate it. If you would I want to help out in this process by adding a few updates based on the submissions I have seen. The concept I think that is coming close to hitting the mark is Corvo Graphix. What I would like to see changed about the concept is the following: Change the outfits to be more Millennial Career Professional. I have attached some ideas to the brief. I want to replace this picture with one of multiple millennials anywhere from 3 and up. I would like the pic to have diversity in it representing most races of people in the USA. I would like my name beneath quiet summit. I'm not a known author yet so having my name that big my distract from the title of the book. Can we make the title a little bigger and so far I like the background.Thanks, DR Added Friday, September 30, 2016

Target Market(s)

Millennial Career Professionals (18 - 34 age group)

Industry/Entity Type

Life Coaching

Logo Text

Quiet Summit

Requirements
Must have
• communicate something NEW, Bold, Youthful, non-traditional. I want it to stick out while still maintaining a sleek and Professional look.
Nice to have
• something that goes with my brand
• http://www.dariusrenfield.example
Should not have
• Nothing 3D or a logo that is hard to read when placed on stationeries, business cards etc

```html
<!DOCTYPE html>
<html lang="en">
<head>
<meta charset="utf-8">
<title>Quiet Summit – Book Cover</title>
<link href="https://fonts.googleapis.com/css2?family=Anton&family=Montserrat:wght@200;400;600&display=swap" rel="stylesheet">
<style>
  :root {
    --back-top: #2a3342;
    --back-mid: #5a6678;
    --back-bottom: #343c4a;
    --gold-light: #ffe600;
    --gold-deep: #f29a00;
    --sub-slate: #5d6f94;
    --body-text: #ffffff;
    --spine-bg: #4a5d7a;
    --spine-text: #b8cbe6;
    --photo-top: #2f3440;
    --photo-mid: #7d9fc4;
    --photo-low: #c9d9ea;
    --author-navy: #0f2b66;
    --frame-line: #6b7688;
    --frame-fill: #3a424f;
    --code-box: #1b1c22;
  }
  * { margin: 0; padding: 0; box-sizing: border-box; }
  html, body { width: 1200px; height: 902px; overflow: hidden; background: #ffffff; }
  .cover { position: relative; width: 1200px; height: 902px; font-family: "Montserrat", sans-serif; }

  .back-cover {
    position: absolute; left: 0; top: 0; width: 584px; height: 902px;
    background: radial-gradient(ellipse 70% 55% at 45% 62%, var(--back-mid), var(--back-bottom) 75%),
                linear-gradient(var(--back-top), var(--back-bottom));
  }
  .back-title {
    position: absolute; left: 52px; top: 56px;
    font-family: "Anton", sans-serif; font-size: 46px; line-height: 1; letter-spacing: 2px;
    color: var(--gold-light); text-transform: uppercase;
  }
  .back-subtitle {
    position: absolute; left: 52px; top: 108px; width: 500px;
    font-family: "Anton", sans-serif; font-size: 16px; letter-spacing: 0.5px;
    color: var(--sub-slate); text-transform: uppercase;
  }
  .blurb {
    position: absolute; left: 51px; top: 148px; width: 488px;
    font-size: 13.6px; line-height: 17.7px; color: var(--body-text); text-align: justify;
  }
  .author-photo {
    position: absolute; left: 47px; top: 451px; width: 163px; height: 188px;
    background: var(--frame-fill); border: 1px solid var(--frame-line);
  }
  .about-heading {
    position: absolute; left: 242px; top: 450px;
    font-size: 14px; font-weight: 600; color: var(--body-text); text-transform: uppercase;
  }
  .about-text {
    position: absolute; left: 242px; top: 477px; width: 306px;
    font-size: 13.6px; line-height: 17.7px; color: var(--body-text); text-align: justify;
  }
  .code-box { position: absolute; left: 53px; top: 808px; width: 110px; height: 62px; background: var(--code-box); }

  .spine {
    position: absolute; left: 584px; top: 0; width: 32px; height: 902px; background: var(--spine-bg);
  }
  .spine-text {
    position: absolute; left: 2px; writing-mode: vertical-rl;
    font-weight: 200; font-size: 27px; letter-spacing: 2px; color: var(--spine-text);
    text-transform: uppercase; line-height: 28px;
  }
  .spine-title { top: 60px; }
  .spine-author { top: 576px; }

  .front-cover { position: absolute; left: 616px; top: 0; width: 584px; height: 902px; overflow: hidden; }
  .front-art {
    position: absolute; inset: 0;
    background: radial-gradient(ellipse 80% 40% at 60% 45%, var(--photo-low), transparent 70%),
                linear-gradient(var(--photo-top) 0%, #3f4b5e 25%, var(--photo-mid) 45%, #9fb8d4 70%, var(--photo-low) 100%);
  }
  .front-title {
    position: absolute; left: 40px; top: 54px; width: 504px; text-align: center;
    font-family: "Anton", sans-serif; font-size: 112px; line-height: 110px; letter-spacing: 6px;
    text-transform: uppercase;
    background: linear-gradient(100deg, var(--gold-light) 0%, var(--gold-deep) 30%, var(--gold-light) 50%, var(--gold-deep) 75%, var(--gold-light) 100%);
    -webkit-background-clip: text; background-clip: text; color: transparent;
  }
  .front-subtitle {
    position: absolute; left: 40px; top: 299px; width: 504px; text-align: center;
    font-family: "Anton", sans-serif; font-size: 19px; letter-spacing: 0.5px;
    color: #ffffff; text-transform: uppercase;
  }
  .front-author {
    position: absolute; left: 40px; top: 800px; width: 504px; text-align: center;
    font-family: "Anton", sans-serif; font-size: 60px; line-height: 1; letter-spacing: 2px;
    color: var(--author-navy); text-transform: uppercase;
  }
</style>
</head>
<body>
<div class="cover">
  <section class="back-cover">
    <h2 class="back-title">Quiet Summit</h2>
    <p class="back-subtitle">Steps for Building a Life You Savor at the Office.</p>
    <p class="blurb">Lorem Ipsum is simply dummy text of the printing and typesetting industry. Lorem Ipsum has been the industry's standard dummy text ever since the 1500s, when an unknown printer took a galley of type and scrambled it to make a type specimen book. It has survived not only five centuries, but also the leap into electronic typesetting, remaining essentially unchanged. It was popularised in the 1960s with the release of Typoset sheets containing Lorem Ipsum passages, and more recently with desktop publishing software like Ardent PageForge including versions of Lorem Ipsum. Lorem Ipsum is simply dummy text of the printing and typesetting industry. Lorem Ipsum has been the industry's standard dummy text ever since the 1500s, when an unknown printer took a galley of type and scrambled it to make a type specimen book. It has survived not only five centuries, but also the leap into electronic typesetting, remaining essentially</p>
    <div class="author-photo" role="img" aria-label="Author portrait placeholder"></div>
    <h3 class="about-heading">About Author</h3>
    <p class="about-text">Lorem Ipsum is simply dummy text of the printing and typesetting industry. Lorem Ipsum has been the industry's standard dummy text ever since the 1500s, when an unknown printer took a galley of type and scrambled it to make a type specimen book. It has survived not only five centuries, but also the leap into electronic typesetting, remaining essentially</p>
    <div class="code-box"></div>
  </section>

  <section class="spine">
    <span class="spine-text spine-title">Quiet Summit</span>
    <span class="spine-text spine-author">Darius Renfield</span>
  </section>

  <section class="front-cover">
    <div class="front-art" role="img" aria-label="Group of diverse young professionals standing together against a misty blue sky"></div>
    <h1 class="front-title">Quiet<br>Summit</h1>
    <p class="front-subtitle">Steps for Building a Life You Savor at the Office.</p>
    <p class="front-author">Darius Renfield</p>
  </section>
</div>
</body>
</html>
```